Wordpress Design Project for Bankruptcy Law Office in San Francisco

our current website: www.dorvanelilaw-example.com

we would like to re-design it for wordpress to make it faster and a bit more modern.

content should be similar to what we have there right now but also we do family law

please include logo for law office:

Law Office of Marta K. Dolvenidze

Thank you.
Updates

please see attached word document with logos that we like as an example.

we do tend to like color red.  darker red.

Please submit your design variations and logo as soon as possible.   We would like to go over them and make our decision

Reason: Please create couple of more variations of logo for your design, so we can make our decision what we like the most. Please see word doc for samples: Text: Law Office Of Marta K. Dolvenidze

Reason: final touches

Target Market(s)

bankruptcy and family law clients

Industry/Entity Type

Family Law

Requirements
Must have
• see examples of law sites
http://promo.lexorbin-example.com/testimonials

- new logo: Law Office of Marta K. Dolvenidze
- client intake form
- blog
- contact us form

Nice to have
• - map
- red color
- on the front page a nice photo of SF or a happy family

```html
<!DOCTYPE html>
<html lang="en">
<head>
<meta charset="utf-8">
<title>Law Office of Marta K. Dolvenidze</title>
<link href="https://fonts.googleapis.com/css2?family=Ubuntu:ital,wght@0,400;0,500;1,400&family=PT+Sans:wght@400;700&display=swap" rel="stylesheet">
<style>
:root{
  --blue:#1f78b8;
  --blue-dark:#13609c;
  --navy:#0c3a78;
  --text:#4d4d4d;
  --bg:#f2f2f2;
  --panel:#ffffff;
  --red:#c0201e;
  --yellow:#f4d21f;
  --line:#9a9a9a;
}
*{margin:0;padding:0;box-sizing:border-box}
html,body{width:957px;height:1200px;overflow:hidden;background:var(--bg)}
.page{position:relative;width:1100px;height:1380px;transform:scale(.87);transform-origin:0 0;font-family:"PT Sans",sans-serif;color:var(--text)}
.abs{position:absolute}
.topbar{left:0;top:0;width:1100px;height:6px;background:var(--blue-dark)}
.brand{left:100px;top:24px;display:flex;align-items:center;gap:16px}
.brand-mark{width:56px;height:56px;background:var(--blue)}
.brand-name{font-family:"Ubuntu",sans-serif;font-weight:400;color:var(--blue);line-height:1.15}
.brand-name .l1{font-size:33px;display:block}
.brand-name .l2{font-size:20px;display:block;letter-spacing:1px}
.search{left:852px;top:50px;width:180px;height:25px;border:1px solid #cfcfcf;border-radius:3px;background:#fff;font-size:11px;font-style:italic;color:#aaa;padding:5px 14px;box-shadow:inset 0 1px 2px rgba(0,0,0,.1)}
.search svg{position:absolute;right:6px;top:6px}
.navband{left:0;top:126px;width:1100px;height:28px;background:var(--blue)}
.nav{left:68px;top:115px;width:966px;height:49px;background:linear-gradient(#2a86c6,#13609c);border-radius:3px;display:flex;font-family:"Ubuntu",sans-serif;font-size:13px;color:#fff;box-shadow:0 2px 3px rgba(0,0,0,.2)}
.nav a{display:flex;align-items:center;justify-content:center;border-right:1px solid #0f5690;color:#fff;text-decoration:none}
.nav a:last-child{border-right:0}
.nav a.active{background:linear-gradient(#3494d3,#1b72b2);border-radius:3px 0 0 3px}
.slider{left:68px;top:175px;width:966px;height:300px;border:3px solid #d8d8d8}
.slide-img{width:100%;height:100%;background:linear-gradient(180deg,#8db6df 0%,#a9c6e6 45%,#3a6c9f 62%,#2f5f95 100%)}
.slide-title{left:70px;top:78px;font-family:"Ubuntu",sans-serif;font-size:28px;color:#fff;text-shadow:0 1px 3px rgba(0,0,0,.5)}
.dots{left:26px;top:262px;display:flex;gap:11px}
.dots i{width:10px;height:10px;border-radius:50%;background:#fff;display:block}
.dots i:first-child{background:#b8c4cf}
.panel{left:67px;top:484px;width:968px;height:773px;background:var(--panel)}
.h-blue{font-family:"Ubuntu",sans-serif;color:var(--blue);font-weight:400}
.dotted{border-top:1px dotted var(--line);height:0}
.body-text{font-size:11px;line-height:18px;text-align:justify}
.photo{border-radius:2px}
.num{display:flex;align-items:center;font-family:"Ubuntu",sans-serif;font-size:15.5px;color:var(--blue);white-space:nowrap}
.num b{width:48px;height:48px;border-radius:50%;background:var(--blue-dark);color:#fff;font-weight:400;font-size:22px;display:flex;align-items:center;justify-content:center;margin-right:9px;flex:none}
.btn{font-size:11px;font-weight:700;color:#fff;background:linear-gradient(#2d8ccd,#155e9c);border-radius:2px;display:flex;align-items:center;justify-content:center;box-shadow:0 1px 2px rgba(0,0,0,.3)}
.avatar{left:749px;top:539px;width:50px;height:50px;border:1px solid #1a5f98;padding:2px;background:#fff}
.avatar div{width:100%;height:100%;background:var(--blue)}
.date{color:var(--red);font-style:italic}
.quest{left:753px;top:659px;width:264px;height:88px;border:1px solid #cfcfcf;border-radius:3px;background:linear-gradient(#f1f1f1,#d9d9d9)}
.quest-icon{left:18px;top:18px;width:50px;height:50px;background:#fff;border:1px solid #d6d6d6}
.story-title{font-family:"Ubuntu",sans-serif;font-weight:500;font-size:13px;color:var(--blue)}
.story-text{font-size:11px;line-height:18px}
.story-text p+p{margin-top:5px}
.form{left:723px;top:807px;width:290px;height:427px;background:var(--blue)}
.tab{font-family:"Ubuntu",sans-serif;font-size:17px;white-space:nowrap}
.tab-client{left:140px;top:0;width:150px;height:34px;background:linear-gradient(#f9e37a,var(--yellow));color:var(--blue);padding:8px 18px}
.tab-contact{left:8px;top:10px;color:#fff}
.label{font-size:12px;color:#fff;white-space:nowrap}
.field{background:#fff;height:24px;width:259px;border:1px solid #c9d9e8}
.send{font-size:11px;font-weight:700;color:#fff;background:var(--navy);border-radius:2px;display:flex;align-items:center;justify-content:center}
.foot-links{left:67px;top:1282px;font-size:11.5px;color:#555;white-space:nowrap}
.foot-links span{margin:0 6px;color:#888}
.copy{left:67px;top:1306px;font-size:11.5px;color:#555;white-space:nowrap}
.follow{left:841px;top:1279px;font-family:"Ubuntu",sans-serif;font-size:13px;color:#777}
.social{width:30px;height:30px;border-radius:50%;background:#a5a5a5}
</style>
</head>
<body>
<div class="page">
  <div class="abs topbar"></div>

  <header class="abs brand">
    <div class="brand-mark"></div>
    <div class="brand-name"><span class="l1">LAW OFFICE OF</span><span class="l2">MARTA K. DOLVENIDZE</span></div>
  </header>

  <div class="abs search">Search
    <svg width="12" height="12" viewBox="0 0 12 12"><circle cx="5" cy="5" r="3.5" fill="none" stroke="#bbb" stroke-width="1.3"/><line x1="7.5" y1="7.5" x2="11" y2="11" stroke="#bbb" stroke-width="1.5"/></svg>
  </div>

  <div class="abs navband"></div>
  <nav class="abs nav">
    <a class="active" style="width:100px">HOME</a>
    <a style="width:114px">ABOUT US</a>
    <a style="width:108px">LAWYERS</a>
    <a style="width:131px">LATEST NEWS</a>
    <a style="width:150px">LATEST ARTICLES</a>
    <a style="width:150px">PRACTICE AREAS</a>
    <a style="width:125px">CONTACT US</a>
    <a style="width:88px">FAQ</a>
  </nav>

  <section class="abs slider">
    <div class="slide-img" role="img" aria-label="Photo of a red suspension bridge over a bay with a city skyline at dusk"></div>
    <div class="abs slide-title">DUIS AUTE IRURE DOLOR</div>
    <div class="abs dots"><i></i><i></i><i></i><i></i></div>
  </section>

  <main class="abs panel"></main>

  <h2 class="abs h-blue" style="left:87px;top:506px;font-size:17.5px">WELCOME TO COMPLETE BANKRUPTCY INFORMATION</h2>
  <div class="abs dotted" style="left:87px;top:547px;width:623px"></div>
  <p class="abs body-text" style="left:87px;top:567px;width:464px">Sed ut perspiciatis unde omnis iste natus error sit voluptatem accusantium dolor emque laudantium, totam rem aperiam, eaque ipsa quae ab illo invenvoluptatum deleniti atque corrupti quos dolores et quas molestias excepturi sint occaecati cupiditate  Sed ut perspiciatis unde omnis iste natus error sit voluptatem accusantium dolor emque laudantium, totam rem aperiam, eaque ipsa quae ab illo invenvoluptatum deleniti atque corrupti quos dolores et quas molestias excepturi sint occaecati cupiditate <i style="color:var(--blue)">View more</i></p>
  <div class="abs photo" style="left:562px;top:569px;width:156px;height:103px;background:linear-gradient(135deg,#d8c7a3,#9b7b4c 55%,#5d4428)" role="img" aria-label="Photo of a bronze statue holding scales of justice"></div>

  <div class="abs num" style="left:89px;top:703px"><b>01</b>DEBT RELIEF</div>
  <div class="abs num" style="left:247px;top:703px"><b>02</b>FORECLOSURE PREVENTION</div>
  <div class="abs num" style="left:519px;top:703px"><b>03</b>CHAPTER 13</div>

  <h2 class="abs h-blue" style="left:747px;top:507px;font-size:17.5px">MY BLOG</h2>
  <div class="abs avatar"><div></div></div>
  <p class="abs body-text" style="left:815px;top:536px;width:195px">Sed ut perspiciatis unde omnis iste natus error sit voluptatem accusantium dolor emque laudantium, totam rem aperiam, eaque ipsa quae ab illo inven-tore veritatis <span class="date">August 29th, 2012</span></p>
  <div class="abs btn" style="left:953px;top:627px;width:55px;height:24px">More...</div>

  <div class="abs quest">
    <div class="abs quest-icon"></div>
    <div class="abs" style="left:80px;top:18px;font-family:Ubuntu,sans-serif;font-size:14px;color:#555;white-space:nowrap">Client Online Questionnaire</div>
    <div class="abs" style="left:100px;top:48px;font-family:Ubuntu,sans-serif;font-size:18px;font-style:italic;color:var(--blue);display:flex;align-items:center;gap:12px;white-space:nowrap">
      <svg width="16" height="14" viewBox="0 0 16 14"><path d="M0 0L8 7L0 14Z M8 0L16 7L8 14Z" fill="#1f78b8"/></svg>Click here</div>
  </div>

  <div class="abs dotted" style="left:87px;top:772px;width:923px"></div>
  <h3 class="abs h-blue" style="left:87px;top:791px;font-size:17px">Different Types of Bankruptcy and Family Law</h3>
  <div class="abs dotted" style="left:87px;top:824px;width:623px"></div>

  <div class="abs" style="left:87px;top:838px;width:219px;height:145px;background:linear-gradient(135deg,#f0ebe0,#e8c37a 50%,#c98d55)" role="img" aria-label="Photo of a smiling family with two children and a cat"></div>
  <div class="abs story-title" style="left:320px;top:837px">Story TItle line goes here</div>
  <div class="abs story-text" style="left:320px;top:860px;width:350px">
    <p>Lorem ipsum dolor sit amet, consectetuer adipiscing elit. Nam cursus. Morbi ut mi. Nullam enim leo, egestas id, condimentum at, laoreet mattis, massa.</p>
    <p>Sed eleifend nonummy diam. Praesent mauris ante, elementum et, bibendum at, posuere sit amet, nibh. Duis tincidunt lectus quis dui viverra vestibulum.</p>
  </div>
  <div class="abs btn" style="left:600px;top:965px;width:55px;height:24px">More...</div>

  <div class="abs" style="left:87px;top:1039px;width:219px;height:145px;background:linear-gradient(135deg,#3b1d10,#8a4a24 50%,#c28a55)" role="img" aria-label="Photo of a wooden judge's gavel beside law books"></div>
  <div class="abs story-title" style="left:323px;top:1044px">Story TItle line goes here</div>
  <div class="abs story-text" style="left:323px;top:1067px;width:350px">
    <p>Lorem ipsum dolor sit amet, consectetuer adipiscing elit. Nam cursus. Morbi ut mi. Nullam enim leo, egestas id, condimentum at, laoreet mattis, massa.</p>
    <p>Sed eleifend nonummy diam. Praesent mauris ante, elementum et, bibendum at, posuere sit amet, nibh. Duis tincidunt lectus quis dui viverra vestibulum.</p>
  </div>
  <div class="abs btn" style="left:598px;top:1177px;width:56px;height:24px">More...</div>

  <form class="abs form">
    <div class="abs tab tab-contact">CONTACT FORM</div>
    <div class="abs tab tab-client">CLIENT FORM</div>
    <div class="abs label" style="left:20px;top:46px">Name:</div>
    <div class="abs field" style="left:17px;top:66px"></div>
    <div class="abs label" style="left:21px;top:95px">Email:</div>
    <div class="abs field" style="left:17px;top:114px"></div>
    <div class="abs label" style="left:22px;top:144px">Phone:</div>
    <div class="abs field" style="left:17px;top:163px"></div>
    <div class="abs label" style="left:22px;top:191px">Subject:</div>
    <div class="abs field" style="left:17px;top:212px"></div>
    <div class="abs label" style="left:23px;top:240px">Message:</div>
    <div class="abs field" style="left:18px;top:261px;height:67px"></div>
    <div class="abs" style="left:20px;top:339px;width:10px;height:10px;background:#fff"></div>
    <div class="abs label" style="left:38px;top:336px;font-size:11px">Send a copy of this message to yourself</div>
    <div class="abs send" style="left:19px;top:369px;width:59px;height:24px">SEND</div>
    <div class="abs send" style="left:92px;top:369px;width:58px;height:24px">RESET</div>
  </form>

  <div class="abs foot-links">Home<span>|</span>About us<span>|</span>Lawyers<span>|</span>Latest News<span>|</span>Latest Articles<span>|</span>Practice Areas<span>|</span>Contact us<span>|</span>FAQ</div>
  <div class="abs copy">Copyright © 2012 www.dorvanelilaw-example.com &nbsp;&nbsp; All rights reserved.</div>

  <div class="abs" style="left:682px;top:1278px;width:76px;height:76px;border-radius:50%;background:#b8954a"></div>

  <div class="abs follow">FOLLOW US</div>
  <div class="abs social" style="left:840px;top:1304px"></div>
  <div class="abs social" style="left:883px;top:1304px"></div>

  <div class="abs" style="left:937px;top:1279px;width:78px;height:68px;background:#5b86c2"></div>
</div>
</body>
</html>
```